Harborline Auto LLC

Car Dealer Customer Service
Address: 2874 Cresthaven Road, Shelbyville, TN 37162
web: www.harborlineautoxq.net
email: harborlineautoxq@mailnest.example
Phone: (931) 555-0148
Phone: (629) 555-0173

```html
<!DOCTYPE html>
<html lang="en">
<head>
<meta charset="utf-8">
<title>Harborline Auto – Business Card</title>
<link rel="stylesheet" href="https://fonts.googleapis.com/css2?family=Montserrat:wght@400;500;700;800&display=swap">
<style>
  :root {
    --stage: #333333;
    --brand-blue: #1c7bad;
    --accent-blue: #2b93cf;
    --brand-gold: #ecb243;
    --paper: #ffffff;
    --ink: #111111;
  }
  * { box-sizing: border-box; margin: 0; padding: 0; }
  html, body {
    width: 1200px; height: 984px; overflow: hidden;
    background: var(--stage);
    font-family: "Montserrat", Arial, sans-serif;
  }
  .canvas { position: relative; width: 1200px; height: 984px; }
  .card {
    position: absolute; left: 220px; width: 760px; height: 434px;
    overflow: hidden;
  }
  .card--front { top: 38px; background: var(--brand-blue); }
  .card--back { top: 510px; background: var(--paper); }

  /* front */
  .front-mark {
    position: absolute; left: 0; right: 0; top: 150px;
    display: flex; flex-direction: column; align-items: center; gap: 28px;
  }
  .front-mark__dot {
    width: 84px; height: 84px; border-radius: 50%;
    background: var(--brand-gold);
  }
  .front-mark__name {
    color: var(--paper); font-weight: 800; font-size: 42px;
    letter-spacing: 1px; text-transform: uppercase;
  }

  /* back */
  .back-mark {
    position: absolute; left: 58px; top: 44px;
    display: flex; flex-direction: column; align-items: center; gap: 16px;
    width: 300px;
  }
  .back-mark__dot {
    width: 70px; height: 70px; border-radius: 50%;
    background: var(--brand-gold);
  }
  .back-mark__name {
    color: var(--brand-blue); font-weight: 800; font-size: 27px;
    letter-spacing: 0.5px; text-transform: uppercase; white-space: nowrap;
  }
  .contact-list {
    position: absolute; left: 54px; top: 226px; list-style: none;
    display: flex; flex-direction: column; gap: 9px;
  }
  .contact-list__item {
    display: flex; align-items: center; gap: 14px;
    font-size: 19px; color: var(--ink); font-weight: 500;
  }
  .contact-list__icon { width: 18px; height: 18px; flex: none; fill: var(--accent-blue); }
  .address {
    position: absolute; right: 70px; top: 266px; text-align: right;
    font-size: 19px; line-height: 1.3; color: var(--ink); font-weight: 500;
  }
  .address-bar {
    position: absolute; right: 40px; top: 300px;
    width: 18px; height: 72px; background: var(--accent-blue);
  }
</style>
</head>
<body>
<main class="canvas">
  <section class="card card--front" aria-label="Card front">
    <div class="front-mark">
      <span class="front-mark__dot"></span>
      <h1 class="front-mark__name">Harborline Auto</h1>
    </div>
  </section>

  <section class="card card--back" aria-label="Card back">
    <div class="back-mark">
      <span class="back-mark__dot"></span>
      <h2 class="back-mark__name">Harborline Auto</h2>
    </div>

    <ul class="contact-list">
      <li class="contact-list__item">
        <svg class="contact-list__icon" viewBox="0 0 24 24" aria-hidden="true"><path d="M6.6 10.8a15 15 0 0 0 6.6 6.6l2.2-2.2a1 1 0 0 1 1-.25 11.4 11.4 0 0 0 3.6.57 1 1 0 0 1 1 1V20a1 1 0 0 1-1 1A17 17 0 0 1 3 4a1 1 0 0 1 1-1h3.5a1 1 0 0 1 1 1c0 1.25.2 2.45.57 3.57a1 1 0 0 1-.25 1z"/></svg>
        (931) 555-0148
      </li>
      <li class="contact-list__item">
        <svg class="contact-list__icon" viewBox="0 0 24 24" aria-hidden="true"><path d="M2 8c0-2 4-4 10-4s10 2 10 4v2h-5V8H7v2H2z"/><rect x="4" y="11" width="16" height="9" rx="1.5"/></svg>
        (629) 555-0173
      </li>
      <li class="contact-list__item">
        <svg class="contact-list__icon" viewBox="0 0 24 24" aria-hidden="true"><path d="M2 5h20v14H2z M2 5l10 8 10-8" stroke="#fff" stroke-width="1.5"/></svg>
        harborlineautoxq@mailnest.example
      </li>
      <li class="contact-list__item">
        <svg class="contact-list__icon" viewBox="0 0 24 24" aria-hidden="true"><circle cx="12" cy="12" r="10"/><path d="M2 12h20M12 2c3 3 3 17 0 20M12 2c-3 3-3 17 0 20" stroke="#fff" stroke-width="1.3" fill="none"/></svg>
        www.harborlineautoxq.net
      </li>
    </ul>

    <address class="address" style="font-style: normal;">
      Car Dealer Customer Service<br>
      2874 Cresthaven Road<br>
      Shelbyville, TN 37162
    </address>
    <span class="address-bar"></span>
  </section>
</main>
</body>
</html>
```